The Brandwell Firm

We need a new design for our letterhead and envelopes. We are a personal injury and criminal defense firm so we need something modern and clean, but more on the professional/traditional side. Our new logo has two colors and is attached to the file so we need something that works well with those colors/matches the design. The following information needs to be on the letterhead:
Phone: (555) 214-3370
Fax: (555) 214-5186
Toll-Free: (888) 431-2059
Post Office Box 4721
Millbrook, SC 29555-4721
HarmClaimCounsel.example
PalmettoTrialAdvocates.example

Target Market(s)

Clients, government agencies, other law firms

Industry/Entity Type

Legal

Font styles to use
Sans Serif
Other font styles liked:
• Arial

Colors

Designer to choose colors to be used in the design.

Requirements
Must have
• Must look professional and clean, modern
Nice to have
• I would like to see a design that works with the logo but does not distract from the content that will be printed on it
Should not have
• Too many colors or crazy designs.

```html
<!DOCTYPE html>
<html lang="en">
<head>
<meta charset="utf-8">
<title>The Brandwell Firm — Stationery</title>
<link href="https://fonts.googleapis.com/css2?family=Roboto:wght@400;500&display=swap" rel="stylesheet">
<style>
  :root {
    --backdrop: #7a7a7a;
    --paper: #f5f4f2;
    --brand-red: #d21f26;
    --brand-blue: #2e3192;
    --ink: #3a3a3a;
    --ink-soft: #555;
  }
  * { box-sizing: border-box; margin: 0; padding: 0; }
  html, body { width: 1200px; height: 793px; overflow: hidden; }
  body {
    background: var(--backdrop);
    font-family: "Roboto", Arial, sans-serif;
    color: var(--ink);
    position: relative;
  }
  .sheet {
    position: absolute;
    background: var(--paper);
    box-shadow: 0 2px 6px rgba(0,0,0,.35);
    overflow: hidden;
  }
  .edge-band { position: absolute; left: 0; top: 0; bottom: 0; background: var(--brand-blue); }
  .edge-band::before { content: ""; position: absolute; left: 0; top: 0; right: 0; background: var(--brand-red); height: var(--red-h); }

  .brand-mark { position: absolute; display: flex; align-items: center; gap: 7px; white-space: nowrap; }
  .brand-mark .dot { width: 14px; height: 14px; border-radius: 50%; background: var(--brand-red); flex: none; }
  .brand-mark .name { font-weight: 500; color: var(--brand-blue); font-size: 19px; letter-spacing: .2px; }

  /* Letterhead */
  .letterhead { left: 82px; top: 62px; width: 475px; height: 668px; }
  .letterhead .edge-band { width: 10px; --red-h: 83px; }
  .letterhead .brand-mark { left: 48px; top: 72px; }
  .contact-block { position: absolute; left: 314px; top: 41px; font-size: 8.2px; line-height: 10.2px; color: var(--ink-soft); }
  .contact-block .address { margin-bottom: 5px; }
  .contact-block li { list-style: none; display: flex; align-items: center; gap: 5px; line-height: 11.2px; }
  .contact-block svg { width: 7px; height: 7px; fill: var(--brand-blue); flex: none; }
  .letter-body { position: absolute; left: 48px; top: 188px; width: 382px; }
  .salutation { font-size: 13px; color: #555; margin-bottom: 22px; }
  .letter-body p.para { font-size: 7.1px; line-height: 11.3px; text-align: justify; margin-bottom: 11.5px; color: #444; }
  .closing { position: absolute; left: 48px; top: 526px; font-size: 7.4px; color: #444; }
  .signature { position: absolute; left: 46px; top: 545px; width: 62px; height: 24px; background: linear-gradient(90deg, #d9d8d6, #c9c8c6); border-radius: 3px; }
  .signatory { position: absolute; left: 48px; top: 580px; font-size: 7.8px; line-height: 10.4px; color: #444; }

  /* Envelope back */
  .envelope-back { left: 578px; top: 225px; width: 530px; height: 241px; }
  .envelope-back .flap { position: absolute; left: 0; top: 0; width: 530px; height: 88px; }
  .envelope-back .brand-mark { left: 50%; top: 34px; transform: translateX(-50%); }
  .envelope-back .brand-mark .dot { background: #fff; width: 11px; height: 11px; }
  .envelope-back .brand-mark .name { color: #fff; font-size: 15px; }

  /* Envelope front */
  .envelope-front { left: 578px; top: 487px; width: 532px; height: 243px; }
  .envelope-front .edge-band { width: 9px; --red-h: 84px; }
  .envelope-front .brand-mark { left: 28px; top: 58px; }
  .return-address { position: absolute; left: 36px; top: 103px; font-size: 8.3px; line-height: 10px; color: var(--ink-soft); }
</style>
</head>
<body>

<section class="sheet letterhead" aria-label="Letterhead">
  <div class="edge-band"></div>
  <div class="brand-mark"><span class="dot"></span><span class="name">The Brandwell Firm</span></div>

  <div class="contact-block">
    <div class="address">Post Office Box 4721<br>Millbrook, SC 29555-4721</div>
    <ul>
      <li><svg viewBox="0 0 10 10"><path d="M2 0.5 L3.8 2.6 L2.8 3.8 Q4 6 6.2 7.2 L7.4 6.2 L9.5 8 L8.3 9.5 Q4 9.2 0.5 1.7Z"/></svg>(888) 431-2059 (TF)</li>
      <li><svg viewBox="0 0 10 10"><path d="M2 0.5 L3.8 2.6 L2.8 3.8 Q4 6 6.2 7.2 L7.4 6.2 L9.5 8 L8.3 9.5 Q4 9.2 0.5 1.7Z"/></svg>(555) 214-3370</li>
      <li><svg viewBox="0 0 10 10"><rect x="2.5" y="1" width="5" height="3"/><rect x="0.5" y="4" width="9" height="4" rx="1"/><rect x="2.5" y="7" width="5" height="2"/></svg>(555) 214-5186</li>
      <li><svg viewBox="0 0 10 10"><circle cx="5" cy="5" r="4.5"/><path d="M0.5 5h9M5 0.5v9" stroke="#f5f4f2" stroke-width=".8"/></svg>HarmClaimCounsel.example</li>
      <li><svg viewBox="0 0 10 10"><circle cx="5" cy="5" r="4.5"/><path d="M0.5 5h9M5 0.5v9" stroke="#f5f4f2" stroke-width=".8"/></svg>PalmettoTrialAdvocates.example</li>
    </ul>
  </div>

  <div class="letter-body">
    <p class="salutation">Dear Mr. Smith,</p>
    <p class="para">Lorem ipsum dolor sit amet, consectetur adipiscing elit. Donec orci purus, luctus vitae dignissim eu, iaculis sed purus. Vivamus faucibus, ipsum nec aliquet viverra, leo mauris condimentum ligula, sit amet sagittis enim ligula quis arcu. Nam egestas tortor id nisi porttitor mattis. In tortor ante, ultricies in suscipit a, tempus non massa. Vivamus et auctor mi. Fusce vel massa nulla. Phasellus nec eros mauris, et scelerisque orci.</p>
    <p class="para">Donec malesuada orci vitae nulla accumsan porta a id massa. Quisque accumsan iaculis magna sit amet fringilla. Maecenas consequat, magna eget tincidunt semper, odio nibh rutrum mi, id feugiat ante nisi eu risus. Vestibulum nunc orci, rhoncus a placerat in, ultricies in mi. Cras mattis varius eros, vel fringilla nisi suscipit eget. Quisque scelerisque sagittis nulla at porttitor.</p>
    <p class="para">Sed id augue vitae urna euismod commodo aliquet a quam. Pellentesque arcu velit, cursus et malesuada ut, consequat et diam. Nullam erat sem, rhoncus id ullamcorper vitae, rhoncus et arcu. In ultricies ultricies nulla, ut rutrum nisi iaculis at. Donec eu magna a metus ornare faucibus. Fusce aliquet faucibus ultricies. Morbi semper, est id tincidunt gravida, sem arcu adipiscing lacus, ac bibendum nulla leo eu purus. Quisque nec diam sed risus consectetur a cursus quis quis nibh. Vestibulum id purus lorem.</p>
    <p class="para">It is a long established fact that a reader will be distracted by the readable content of a page when looking at its layout. The point of using Lorem Ipsum is that it has a more-or-less normal distribution of letters, as opposed to using 'Content here, content here', making it look like readable English. Many desktop publishing packages</p>
  </div>

  <p class="closing">Sincerely,</p>
  <div class="signature" role="img" aria-label="Handwritten signature"></div>
  <p class="signatory">Daniel Reyes<br>CEO/ Founder</p>
</section>

<section class="sheet envelope-back" aria-label="Envelope back">
  <svg class="flap" viewBox="0 0 530 88" aria-hidden="true">
    <path d="M0 0 H530 L519 62 Q514 88 488 88 H42 Q16 88 11 62 Z" fill="var(--brand-red)"/>
  </svg>
  <div class="brand-mark"><span class="dot"></span><span class="name">The Brandwell Firm</span></div>
</section>

<section class="sheet envelope-front" aria-label="Envelope front">
  <div class="edge-band"></div>
  <div class="brand-mark"><span class="dot"></span><span class="name">The Brandwell Firm</span></div>
  <p class="return-address">Post Office Box 4721<br>Millbrook, SC 29555-4721</p>
</section>

</body>
</html>
```